Crestline Plaque & Medal Unique Business Card Design

Recently selected a new logo design and waiting to recieve print files. I've attached image for your review. We are a trophies and awards company that provides engraving on trophies, plaques, name plates, name tags, desk sets, medals, acrylics, and signage.

We are located in Monroe, Louisiana and provide this service with computerized & laser engraving equipment.

Target Market(s)

Corporate, Sport, Church, and Special Events

Industry/Entity Type

Business

Contact Information for Business Card

I'd like to see the following list on the card: Trophies, Plaques, Name Plates, Name Tags, Desk Sets, Medals, Certificates... this is accomplished with Computerized & Laser Engraving

Colors
0555a3
ec1f27
ffffff

Requirements
Must have
• I like either single or double sided. If a design can be created with a frosted card stock I'd consider single. Must be Red, White, and Blue. Dwight Palmer - Owner, 412 W 8th Ave, Monroe, La 71208 office 318-555-0148 fax 318-555-0163 email: info@crestlineplaquemedal.example, and website: www.crestlineplaquemedal.example

```html
<!DOCTYPE html>
<html lang="en">
<head>
<meta charset="utf-8">
<title>Crestline Plaque &amp; Medal – Business Card</title>
<link rel="stylesheet" href="https://fonts.googleapis.com/css2?family=Open+Sans:wght@400;600;700&display=swap">
<style>
  :root {
    --brand-blue: #0555a3;
    --brand-red: #ec1f27;
    --brand-white: #ffffff;
    --band-light: #6fa4dc;
    --ink: #1c1c1c;
    --ink-soft: #444a52;
    --backdrop: #e6e7e9;
  }
  * { margin: 0; padding: 0; box-sizing: border-box; }
  html, body { width: 1200px; height: 800px; overflow: hidden; }
  body {
    background: var(--backdrop);
    font-family: "Open Sans", Arial, sans-serif;
    position: relative;
  }
  .card {
    position: absolute;
    top: 252px;
    width: 520px;
    height: 297px;
    background: var(--brand-white);
    border-radius: 4px;
    box-shadow: 0 6px 18px rgba(0,0,0,.15);
    overflow: hidden;
  }
  .card--contact { left: 50px; }
  .card--products { left: 630px; }
  .card__band {
    position: absolute; left: 0; right: 0; bottom: 0; height: 24px;
    background: linear-gradient(90deg, var(--brand-blue), var(--band-light));
  }
  .card--contact .card__band {
    right: 180px;
    background: linear-gradient(90deg, var(--brand-blue) 0%, var(--band-light) 80%, rgba(111,164,220,0) 100%);
  }
  .wordmark {
    display: flex; align-items: center; gap: 8px;
    color: var(--brand-blue); font-weight: 700; line-height: 1.05;
  }
  .wordmark__dot {
    flex: none; border-radius: 50%; background: var(--brand-red);
  }
  .card--contact .wordmark { position: absolute; left: 36px; top: 34px; font-size: 20px; width: 200px; }
  .card--contact .wordmark__dot { width: 16px; height: 16px; }
  .divider { position: absolute; left: 150px; top: 118px; }
  .contact {
    position: absolute; left: 262px; top: 138px;
  }
  .contact__name { font-size: 21px; font-weight: 700; color: var(--ink); line-height: 1; }
  .contact__name .first { color: var(--brand-red); }
  .contact__role { font-size: 11px; font-weight: 700; color: var(--ink); margin: 3px 0 10px; }
  .contact__list { list-style: none; font-size: 10.5px; color: var(--ink-soft); }
  .contact__list li { display: flex; align-items: center; gap: 7px; height: 17px; }
  .contact__list svg { flex: none; }
  .card--products .wordmark {
    position: absolute; left: 0; right: 0; top: 78px; justify-content: center;
    font-size: 32px;
  }
  .card--products .wordmark__dot { width: 22px; height: 22px; }
  .rule {
    position: absolute; left: 95px; right: 95px; top: 130px; height: 2px;
    background: var(--brand-blue);
  }
  .products { position: absolute; left: 0; right: 0; top: 168px; text-align: center; color: var(--brand-blue); font-weight: 700; }
  .products__label { font-size: 12px; margin-bottom: 6px; }
  .products__list { font-size: 11px; }
  .products__list .sep { color: var(--brand-red); margin: 0 4px; }
</style>
</head>
<body>

<section class="card card--contact" aria-label="Business card, contact side">
  <div class="wordmark"><span class="wordmark__dot"></span><span>Crestline Plaque &amp; Medal</span></div>

  <svg class="divider" width="300" height="40" viewBox="0 0 300 40" aria-hidden="true">
    <path d="M0 38 L300 0 L300 1.5 Z" fill="var(--brand-blue)" opacity=".6"/>
  </svg>

  <div class="contact">
    <p class="contact__name"><span class="first">Dwight</span> Palmer</p>
    <p class="contact__role">Owner</p>
    <ul class="contact__list">
      <li><svg width="11" height="11" viewBox="0 0 12 12"><rect width="12" height="12" rx="2" fill="var(--brand-red)"/><path d="M3.5 2.5h2l.6 2-1 .8a5 5 0 0 0 1.6 1.6l.8-1 2 .6v2c0 .6-.4 1-1 1A6.5 6.5 0 0 1 2.5 3.5c0-.6.4-1 1-1z" fill="#fff"/></svg>318-555-0148</li>
      <li><svg width="11" height="11" viewBox="0 0 12 12"><rect width="12" height="12" rx="2" fill="var(--brand-red)"/><rect x="3" y="2.5" width="6" height="3" fill="#fff"/><rect x="2" y="5.5" width="8" height="4" rx="1" fill="#fff"/></svg>(318)-555-0192</li>
      <li><svg width="11" height="11" viewBox="0 0 12 12"><rect width="12" height="12" rx="2" fill="var(--brand-red)"/><rect x="2.5" y="3.5" width="7" height="5" fill="#fff"/><path d="M2.5 3.5L6 6.5 9.5 3.5" stroke="var(--brand-red)" fill="none"/></svg>info@crestlineplaquemedal.example</li>
      <li><svg width="11" height="11" viewBox="0 0 12 12"><rect width="12" height="12" rx="2" fill="var(--brand-red)"/><circle cx="6" cy="6" r="3.3" fill="none" stroke="#fff"/><path d="M2.7 6h6.6M6 2.7v6.6" stroke="#fff" stroke-width=".8"/></svg>www.crestlineplaquemedal.example</li>
      <li><svg width="11" height="11" viewBox="0 0 12 12"><rect width="12" height="12" rx="2" fill="var(--brand-red)"/><path d="M6 2.2a2.6 2.6 0 0 1 2.6 2.6C8.6 6.8 6 9.8 6 9.8S3.4 6.8 3.4 4.8A2.6 2.6 0 0 1 6 2.2z" fill="#fff"/><circle cx="6" cy="4.8" r="1" fill="var(--brand-red)"/></svg>412 W 8th Ave, Monroe, La 71208</li>
    </ul>
  </div>

  <div class="card__band"></div>
</section>

<section class="card card--products" aria-label="Business card, products side">
  <div class="wordmark"><span class="wordmark__dot"></span><span>Crestline Plaque &amp; Medal</span></div>
  <div class="rule"></div>
  <div class="products">
    <p class="products__label">Our Products:</p>
    <p class="products__list">Trophies<span class="sep">|</span>Plaques<span class="sep">|</span>Name Plates<span class="sep">|</span>Name Tags<span class="sep">|</span>Desk Sets<span class="sep">|</span>Medals<span class="sep">|</span>Certificates...</p>
  </div>
  <div class="card__band"></div>
</section>

</body>
</html>
```